Dental Practice Billboard Design

We are a newer dental practice in need of a simple but appealing billboard for our growing dental practice to attract new patients. The practice is owned by husband and wife dentists and is family friendly in a small town in Kentucky. We try to be very friendly and caring to our patients. Would prefer a blue background for the billboard and our tooth logo to be prominent. We are partial to the Patua One font used in the image below but please feel free to tweak it as you deem necessary. The shape of the uppercase D and lowercase g are why we like that font, so fonts with a similarly shaped “D” and “g” would work as well. Please include our phone number (555) 847-1390. Please see our website Harlowbrookdentistry.example for more info on the practice if needed. Thank you! Looking forward to seeing your creation.
Updates

The dimensions will be 12ft x 24ft (3.6576m x 7.3152m). Apologies for not including this in the original prompt. Thank you all for your submissions.

Industry/Entity Type

Dental

Font styles to use
Other font styles liked:
• Patua One

Colors
0054AA
0677BA
7BADD7
CADEEF
E8F1F8
0094D4
00A9DD
6FCCEA
C7EBF8
E9F6FB
00AB8E
00BBA5
67D7C9
C6EFE9
E9F9F6
59FF00
82FF00
B8FF75
E3FFCB
F4FFEA

Requirements
Must have
• Phone number, website, Logo, Practice name “Harlow Brook Dentistry”
Should not have
• A tagline or slogan

```html
<!DOCTYPE html>
<html lang="en">
<head>
<meta charset="utf-8">
<title>Harlow Brook Dentistry – Billboard</title>
<link rel="stylesheet" href="https://fonts.googleapis.com/css2?family=Patua+One&display=swap">
<style>
  :root {
    --navy-deep: #062a66;
    --blue-bright: #0a57c2;
    --green: #12a80c;
    --white: #ffffff;
    --text-font: "Patua One", Georgia, serif;
  }
  html, body {
    margin: 0;
    padding: 0;
    width: 1200px;
    height: 722px;
    overflow: hidden;
    background: #f2f4f7;
  }
  .billboard {
    position: relative;
    width: 1200px;
    height: 722px;
    overflow: hidden;
    background: radial-gradient(ellipse at 85% 20%, var(--blue-bright) 0%, #0645a0 40%, var(--navy-deep) 80%);
    font-family: var(--text-font);
  }
  .brand {
    position: absolute;
    left: 46px;
    top: 230px;
    display: flex;
    align-items: center;
    gap: 22px;
  }
  .brand-dot {
    width: 92px;
    height: 92px;
    border-radius: 50%;
    background: var(--green);
    flex: none;
  }
  .brand-name {
    color: var(--white);
    line-height: 1;
  }
  .brand-name .primary {
    display: block;
    font-size: 76px;
  }
  .brand-name .secondary {
    display: block;
    font-size: 52px;
    margin-top: 8px;
  }
  .team-photo {
    position: absolute;
    left: 640px;
    top: 96px;
    width: 560px;
    height: 494px;
    background: linear-gradient(180deg, #2a5db8 0%, #c9d6e8 55%, #eef1f5 100%);
  }
  .bands {
    position: absolute;
    inset: 0;
    width: 1200px;
    height: 722px;
  }
  .phone {
    position: absolute;
    left: 30px;
    top: 620px;
    display: flex;
    align-items: center;
    gap: 16px;
    color: var(--green);
    font-size: 72px;
    line-height: 1;
  }
  .website {
    position: absolute;
    left: 662px;
    right: 24px;
    top: 634px;
    display: flex;
    align-items: center;
    gap: 14px;
    color: var(--white);
    font-size: 29px;
    line-height: 1;
    white-space: nowrap;
  }
  .website svg {
    flex: none;
  }
</style>
</head>
<body>
  <main class="billboard">
    <div class="team-photo" role="img" aria-label="Photo of the two dentists in white coats, smiling"></div>

    <svg class="bands" viewBox="0 0 1200 722" aria-hidden="true">
      <polygon points="0,600 560,600 625,722 0,722" fill="var(--white)"/>
      <polygon points="595,590 1200,590 1200,722 660,722" fill="var(--green)"/>
    </svg>

    <div class="brand">
      <span class="brand-dot"></span>
      <div class="brand-name">
        <span class="primary">Harlow Brook</span>
        <span class="secondary">Dentistry</span>
      </div>
    </div>

    <div class="phone">
      <svg width="58" height="58" viewBox="0 0 58 58" aria-hidden="true">
        <circle cx="29" cy="29" r="29" fill="var(--green)"/>
        <path d="M20 15c2-1 4 0 5 2l2 5c1 2 0 3-1 4l-2 2c2 4 5 7 9 9l2-2c1-1 2-2 4-1l5 2c2 1 3 3 2 5l-2 3c-1 2-3 2-5 2-12-2-22-12-24-24 0-2 0-4 2-5z" fill="var(--white)"/>
      </svg>
      <span>(555) 847-1390</span>
    </div>

    <div class="website">
      <svg width="42" height="35" viewBox="0 0 46 38" aria-hidden="true">
        <rect x="7" y="3" width="32" height="23" rx="2" fill="none" stroke="var(--white)" stroke-width="4"/>
        <rect x="1" y="29" width="44" height="6" rx="2" fill="var(--white)"/>
      </svg>
      <span>Harlowbrookdentistry.example</span>
    </div>
  </main>
</body>
</html>
```